Create an awesome website for a medical clinic

This is a new website for a doctor's office. The site should be clean and modern, easy to navigate.

This is a wellness clinic, we want to help our clients have a healthy, active lifestyle. It should be friendly and inviting, and easy for them to call or schedule an appointment.

The site should be responsive and designed using the attached Bootstrap 3 PSD.

We will provide stock photos, until then please use stock photos from:

pixelharbor.com or
framequarry.com (preferred)

Some example sites of clean and modern designs that we like:

https://tulsaspinecare.com/
http://reachpastjoints.com/
http://turninghealthier.com/

Also attached is a temporary logo you can use.

Reason: Thank you everyone for your great designs - we need a little more time so I'm extending the project.

Need extra days to review

Also, the colors in the new logo I just linked to are the final colors of the logo, so feel free to use any complimentary colors to it.

Hi everyone, The boss wants to change the layout of the site a little bit - here's the revised layout: https://www.filecrate.com/s/k9rt31vx2qp84zn/notes%2011_29_2017.pdf?dl=0 And the graphic assets you can use are here: https://www.filecrate.com/s/k9rt31vx2qp84zn/notes%2011_29_2017.pdf?dl=0 Feel free to change the background color of the "topbar", and change the icons of the "why people trust us" if you want, these are just temporary placeholders. Thanks for your patience and hard work!

Target Market(s)

People seeking medical treatment (wellness clinic)

Industry/Entity Type

Doctor

Number of Pages Required

1 page

Font styles to use
Sans Serif

Colors
0592cd
33a6d7
abd037
9bcb3c

Requirements
Must have
• The home page should have: a strong hero image/slideshow, clinic phone number should be prominent and at the top of the page (in the nav), a "what to expect" section (this is like a FAQs section - see attachment), and a strong call to action (a button to call or schedule an appointment).
• The what to expect section is useful so that prospective clients can determine if we're a good fit for them or not. It's a basic, first-step pre-qualification block of information.
• Social media icons which links to our social media profiles should be included.
Nice to have
• - Link to 3 most recent blog entries
• - Testimonials
• - How a multilevel nav menu looks.

```html
<!DOCTYPE html>
<html lang="en">
<head>
<meta charset="utf-8">
<title>Verdant Wellness Clinic</title>
<link href="https://fonts.googleapis.com/css2?family=Roboto:wght@300;400;500;700&display=swap" rel="stylesheet">
<style>
:root{
  --blue:#33a6d7;
  --blue-deep:#0592cd;
  --green:#9bcb3c;
  --green-deep:#4aa33a;
  --ink:#333a40;
  --muted:#909090;
  --text:#8c8c8c;
  --heading:#6b6b6b;
  --line:#e8eaec;
  --white:#ffffff;
}
*{margin:0;padding:0;box-sizing:border-box}
html,body{width:1200px;height:3232px;overflow:hidden;background:var(--white)}
body{font-family:'Roboto',sans-serif;color:var(--ink);position:relative;-webkit-font-smoothing:antialiased;-moz-osx-font-smoothing:grayscale}
.abs{position:absolute}

/* top bar */
.topbar{position:absolute;left:0;top:0;width:1200px;height:86px;border-bottom:1px solid var(--line)}
.brand{position:absolute;left:99px;top:24px;font-size:23px;font-weight:700;color:var(--green-deep);letter-spacing:.3px;line-height:1}
.brand small{display:block;font-size:10px;font-weight:700;letter-spacing:.8px;margin-top:4px}
.info{position:absolute;top:22px;display:flex;gap:13px;align-items:flex-start}
.info .ico{width:36px;height:36px;border-radius:50%;display:flex;align-items:center;justify-content:center;flex:none}
.info .ico.blue{background:var(--blue)}
.info .ico.green{background:var(--green)}
.info h4{font-size:13px;font-weight:500;color:#555;margin-top:3px}
.info p{font-size:11px;font-weight:300;color:var(--muted);margin-top:3px}

/* nav */
.navbar{position:absolute;left:0;top:86px;width:1200px;height:63px;border-bottom:1px solid var(--line)}
.social{position:absolute;left:99px;top:15px;display:flex;gap:13px}
.social span{width:31px;height:31px;border:1.5px solid var(--blue);border-radius:50%;display:flex;align-items:center;justify-content:center}
.menu{position:absolute;top:26px;font-size:12.5px;color:#777;font-weight:400;list-style:none}
.menu li{position:absolute;white-space:nowrap}
.book{position:absolute;left:924px;top:17px;width:177px;height:31px;background:var(--blue);color:var(--white);font-size:10.5px;font-weight:500;display:flex;align-items:center;justify-content:center;border-radius:2px;letter-spacing:.2px}

/* hero */
.hero{position:absolute;left:0;top:149px;width:1200px;height:439px;overflow:hidden}
.hero-photo{position:absolute;inset:0;background:linear-gradient(180deg,#7d8285 0%,#8a8c8a 45%,#6d6a55 68%,#4e4a33 100%)}
.hero h1{position:absolute;left:0;width:1200px;top:154px;text-align:center;color:var(--white);font-size:27px;font-weight:500;letter-spacing:.2px}
.hero p{position:absolute;left:0;width:1200px;top:194px;text-align:center;color:#f2f2f2;font-size:18px;font-weight:300}
.hero .btn{position:absolute;left:511px;top:245px;width:178px;height:30px;background:var(--blue);color:var(--white);font-size:10.5px;display:flex;align-items:center;justify-content:center;border-radius:2px}

/* section titles */
.section-title{position:absolute;left:0;width:1200px;text-align:center;font-size:21px;font-weight:400;color:#6a6f74;letter-spacing:.4px}
.down-arrow{position:absolute;left:585px;width:30px;height:32px}

/* conditions grid */
.condition{position:absolute;width:317px}
.condition .photo{height:142px}
.condition p{margin-top:18px;font-size:15px;color:var(--text);font-weight:400}

/* call to action band */
.cta-band{position:absolute;left:0;top:1295px;width:1200px;height:585px}
.cta-band svg{position:absolute;inset:0}
.cta-doctor{position:absolute;left:118px;top:170px;width:367px;height:377px;border-radius:4px}
.cta-copy{position:absolute;left:614px;top:180px;width:430px;color:var(--white)}
.cta-copy h2{font-size:22px;font-weight:500;letter-spacing:.3px}
.cta-copy p{font-size:11.5px;line-height:16px;font-weight:300;margin-top:10px;color:#eef6fa}
.cta-copy p + p{margin-top:4px}
.cta-copy .btn-outline{display:inline-flex;margin-top:18px;width:194px;height:30px;border:1px solid var(--white);align-items:center;justify-content:center;font-size:10.5px;border-radius:2px}

/* visits */
.visit-photo{position:absolute;width:405px;height:233px}
.visit-copy{position:absolute;width:505px}
.visit-copy h3{font-size:19px;font-weight:500;color:var(--heading)}
.visit-copy p{margin-top:6px;font-size:15px;line-height:25px;color:var(--text);font-weight:400}
</style>
</head>
<body>

<header class="topbar">
  <div class="brand">VERDANT<small>WELLNESS CLINIC</small></div>

  <div class="info" style="left:394px">
    <div class="ico blue"><svg width="16" height="18" viewBox="0 0 16 18"><path d="M8 1a6 6 0 0 0-6 6c0 4.5 6 10 6 10s6-5.5 6-10a6 6 0 0 0-6-6z" fill="#fff"/><circle cx="8" cy="7" r="2.2" fill="#33a6d7"/></svg></div>
    <div><h4>Our Address</h4><p>418 W Cedar Row Lane, Maple Falls.</p></div>
  </div>
  <div class="info" style="left:694px">
    <div class="ico green"><svg width="18" height="18" viewBox="0 0 18 18"><circle cx="9" cy="9" r="7" fill="#fff"/><path d="M9 5v4.5l3 2" stroke="#9bcb3c" stroke-width="1.8" fill="none" stroke-linecap="round"/></svg></div>
    <div><h4>Open Hours</h4><p>Mon - Friday: 8AM - 5PM</p></div>
  </div>
  <div class="info" style="left:935px">
    <div class="ico blue"><svg width="16" height="16" viewBox="0 0 16 16"><path d="M3.2 1.5l2.6 2.8-1.3 2.2c1 2 2.8 3.8 5 5l2.2-1.3 2.8 2.6-1.6 2C7.5 14.5 1.5 8.5 1.2 3.1z" fill="#fff"/></svg></div>
    <div><h4>Give us a Call</h4><p>+1 (555) 014-2290</p></div>
  </div>
</header>

<nav class="navbar">
  <div class="social" aria-label="Social profiles">
    <span><svg width="13" height="13" viewBox="0 0 13 13"><circle cx="3" cy="6.5" r="1.8" fill="#33a6d7"/><circle cx="10" cy="2.5" r="1.8" fill="#33a6d7"/><circle cx="10" cy="10.5" r="1.8" fill="#33a6d7"/><path d="M3 6.5L10 2.5M3 6.5L10 10.5" stroke="#33a6d7" stroke-width="1.1"/></svg></span>
    <span><svg width="13" height="12" viewBox="0 0 13 12"><path d="M1.5 1.5h10v7h-6l-3 2.5v-2.5h-1z" fill="none" stroke="#33a6d7" stroke-width="1.3" stroke-linejoin="round"/></svg></span>
    <span><svg width="13" height="12" viewBox="0 0 13 12"><path d="M6.5 11S1 7.6 1 4.1A2.7 2.7 0 0 1 6.5 3a2.7 2.7 0 0 1 5.5 1.1C12 7.6 6.5 11 6.5 11z" fill="none" stroke="#33a6d7" stroke-width="1.3"/></svg></span>
  </div>
  <ul class="menu">
    <li style="left:373px">HOME</li>
    <li style="left:455px">SERVICES <svg width="11" height="7" viewBox="0 0 11 7" style="margin-left:6px"><path d="M1 1l4.5 4.5L10 1" stroke="#888" stroke-width="1.2" fill="none"/></svg></li>
    <li style="left:580px">ABOUT</li>
    <li style="left:668px">BLOG</li>
    <li style="left:745px">CONTACT US</li>
  </ul>
  <div class="book">BOOK AN APPOINTMENT</div>
</nav>

<section class="hero">
  <div class="hero-photo" role="img" aria-label="Woman stretching her arms in a wheat field"></div>
  <h1>WE ARE A UNIQUE PHYSICAL THERAPY CLINIC</h1>
  <p>Lorem ipsum dolor set ame sdipiscing at vero</p>
  <div class="btn">CONTACT US</div>
</section>

<h2 class="section-title" style="top:680px">DO YOU SUFFER FROM ANY OF THE FOLLOWING?</h2>
<svg class="down-arrow" style="top:726px" viewBox="0 0 30 32"><path d="M15 1v29M4 19l11 11 11-11" stroke="#33a6d7" stroke-width="1.5" fill="none"/></svg>

<div class="condition" style="left:99px;top:825px"><div class="photo" role="img" aria-label="Doctor reviewing an x-ray with a patient" style="background:linear-gradient(135deg,#c9dbe6,#e9eef1 60%,#b9c9d2)"></div><p>Lorem ipsum dolor set amet</p></div>
<div class="condition" style="left:442px;top:825px"><div class="photo" role="img" aria-label="Patient receiving a facial treatment" style="background:linear-gradient(135deg,#3a2f2b,#c49a85 55%,#e8e1dc)"></div><p>Lorem ipsum dolor set amet</p></div>
<div class="condition" style="left:784px;top:825px"><div class="photo" role="img" aria-label="Doctor consulting with a couple" style="background:linear-gradient(135deg,#e9eef2,#9fb8c8 55%,#e5ecf0)"></div><p>Lorem ipsum dolor set amet</p></div>
<div class="condition" style="left:99px;top:1058px"><div class="photo" role="img" aria-label="Doctor talking with a senior patient" style="background:linear-gradient(135deg,#f3f4f4,#d7dfe5 55%,#eef1f3)"></div><p>Lorem ipsum dolor set amet</p></div>
<div class="condition" style="left:442px;top:1058px"><div class="photo" role="img" aria-label="Woman holding her temples with a headache" style="background:linear-gradient(135deg,#ffffff,#ecd6c8 55%,#ffffff)"></div><p>Lorem ipsum dolor set amet</p></div>
<div class="condition" style="left:784px;top:1058px"><div class="photo" role="img" aria-label="Young woman on a hospital drip" style="background:linear-gradient(135deg,#f4f6f8,#c8d2da 55%,#5a4a44)"></div><p>Lorem ipsum dolor set amet</p></div>

<section class="cta-band">
  <svg width="1200" height="585" viewBox="0 0 1200 585">
    <defs>
      <linearGradient id="bandFill" x1="0" y1="0" x2="1" y2="0.3">
        <stop offset="0" stop-color="#7fb7d6"/>
        <stop offset=".5" stop-color="#4f93bd"/>
        <stop offset="1" stop-color="#7ab3ca"/>
      </linearGradient>
    </defs>
    <polygon points="0,159 1200,0 1200,428 0,585" fill="url(#bandFill)"/>
  </svg>
  <div class="cta-doctor" role="img" aria-label="Smiling female doctor in a white coat with a stethoscope" style="background:linear-gradient(180deg,rgba(255,255,255,0) 0%,rgba(236,241,245,.55) 45%,#f1f4f6 100%)"></div>
  <div class="cta-copy">
    <h2>ARE YOU READY TO FEEL BETTER?</h2>
    <p>Sed ut perspiciatis unde omnis iste natus error sit voluptatem accusantium doloremque laudantium, totam rem aperiam, eaque ipsa quae ab illo inventore veritatis et quasi architecto beatae vitae dicta sunt explicabo.</p>
    <p>Sed ut perspiciatis unde omnis iste natus error sit voluptatem accus adoloremque laudantium, totam rem aperiam, eaque ipsa quae ab illo inventore veritatis et quasi architecto beatae.</p>
    <div class="btn-outline">SCHEDULE AN APPOINMENT</div>
  </div>
</section>

<h2 class="section-title" style="top:1904px">WHAT TO EXPECT</h2>
<svg class="down-arrow" style="top:1950px" viewBox="0 0 30 32"><path d="M15 1v29M4 19l11 11 11-11" stroke="#33a6d7" stroke-width="1.5" fill="none"/></svg>

<div class="visit-photo" style="left:99px;top:2051px;background:linear-gradient(135deg,#d9e3e8,#f4f7f8 50%,#c8d5dc)" role="img" aria-label="Smiling nurse standing in a bright clinic room"></div>
<div class="visit-copy" style="left:612px;top:2092px">
  <h3>Visit 1</h3>
  <p>Lorem ipsum dolor sit amet, consectetur adipiscing elit, sed do eiusmod tempor incididunt ut labore et dolore magna aliqua. Ut enim ad minim veniam, quis nostrud exercitation ullamco laboris nisi ut aliquip ex ea commodo consequat. But I must explain to you how all this mistaken idea of denouncing pleasure.</p>
</div>

<div class="visit-copy" style="left:99px;top:2369px">
  <h3>Visit 2</h3>
  <p>Lorem ipsum dolor sit amet, consectetur adipiscing elit, sed do eiusmod tempor incididunt ut labore et dolore magna aliqua. Ut enim ad minim veniam, quis nostrud exercitation ullamco laboris nisi ut aliquip ex ea commodo consequat. But I must explain to you how all this mistaken idea of denouncing pleasure.</p>
</div>
<div class="visit-photo" style="left:696px;top:2328px;background:linear-gradient(135deg,#e6ecef,#b7c6d2 50%,#56677a)" role="img" aria-label="Doctor listening to a patient in consultation"></div>

<div class="visit-photo" style="left:99px;top:2606px;background:linear-gradient(135deg,#eef2f4,#c4d4de 45%,#f5f6f7)" role="img" aria-label="Female doctor with colleagues working in the background"></div>
<div class="visit-copy" style="left:612px;top:2647px">
  <h3>Visit 3</h3>
  <p>Lorem ipsum dolor sit amet, consectetur adipiscing elit, sed do eiusmod tempor incididunt ut labore et dolore magna aliqua. Ut enim ad minim veniam, quis nostrud exercitation ullamco laboris nisi ut aliquip ex ea commodo consequat. But I must explain to you how all this mistaken idea of denouncing pleasure.</p>
</div>

<div class="visit-copy" style="left:99px;top:2925px">
  <h3>Visit 4</h3>
  <p>Lorem ipsum dolor sit amet, consectetur adipiscing elit, sed do eiusmod tempor incididunt ut labore et dolore magna aliqua. Ut enim ad minim veniam, quis nostrud exercitation ullamco laboris nisi ut aliquip ex ea commodo consequat. But I must explain to you how all this mistaken idea of denouncing pleasure.</p>
</div>
<div class="visit-photo" style="left:696px;top:2884px;background:linear-gradient(135deg,#f2f4f5,#9fc4d3 50%,#eef1f3)" role="img" aria-label="Team of four smiling medical staff"></div>

</body>
</html>
```